Business Card Design For A Renovation Contractor Company

We need a business card for a new company based in Singapore, our company name is "RB Tolvane". We are a renovation contractor that builds designs into reality. We build more of F&B restaurants, retail stores and commercial offices. We work very closely with designers. The final design should communicate to our client that we are a company that you can trust, that will plan and complete your project without giving you a headache. I like my client to remember my company as "RB". The beauty of SIMPLE is important.

Industry/Entity Type

Contractor

Requirements
Nice to have
• Black or Red base

```html
<!DOCTYPE html>
<html lang="en">
<head>
<meta charset="utf-8">
<title>RB Tolvane – Business Card</title>
<link rel="stylesheet" href="https://fonts.googleapis.com/css2?family=Jost:wght@400;500;600&display=swap">
<style>
  :root {
    --stage: #ecebe8;
    --card: #ffffff;
    --ink: #1b1b1b;
    --ink-soft: #4a4a4a;
    --accent: #e0202a;
    --rule: #8a8fb0;
    --shadow: rgba(0, 0, 0, 0.14);
  }
  * { box-sizing: border-box; margin: 0; padding: 0; }
  html, body {
    width: 1200px;
    height: 720px;
    overflow: hidden;
    background: var(--stage);
    font-family: "Jost", "Futura", sans-serif;
    color: var(--ink);
  }
  .sheet {
    width: 1200px;
    height: 720px;
    display: flex;
    align-items: center;
    justify-content: center;
    gap: 60px;
  }
  .card {
    position: relative;
    width: 530px;
    height: 303px;
    background: var(--card);
    box-shadow: 0 6px 18px var(--shadow);
  }

  /* Front */
  .brand {
    position: absolute;
    left: 34px;
    top: 40px;
    display: flex;
    align-items: center;
    gap: 12px;
  }
  .brand-dot {
    width: 30px;
    height: 30px;
    border-radius: 50%;
    background: var(--accent);
  }
  .brand-name {
    font-size: 36px;
    font-weight: 500;
    letter-spacing: 0.5px;
    color: var(--ink);
    line-height: 1;
  }
  .tagline {
    position: absolute;
    left: 34px;
    top: 92px;
    width: 222px;
    padding-top: 3px;
    border-top: 2px solid var(--ink-soft);
    font-size: 14px;
    color: var(--ink-soft);
    letter-spacing: 0.3px;
  }
  .person {
    position: absolute;
    left: 34px;
    top: 168px;
  }
  .person-name {
    font-size: 20px;
    font-weight: 600;
    color: var(--accent);
  }
  .person-title {
    font-size: 15px;
    color: var(--ink-soft);
    margin-top: 2px;
  }
  .web {
    position: absolute;
    left: 34px;
    bottom: 30px;
    font-size: 14px;
    letter-spacing: 3px;
    color: var(--ink);
  }
  .web .web-accent { color: var(--accent); }
  .divider {
    position: absolute;
    left: 300px;
    top: 120px;
    width: 1px;
    height: 120px;
    background: var(--rule);
  }
  .contact {
    position: absolute;
    left: 318px;
    top: 110px;
    list-style: none;
    font-size: 14px;
    line-height: 1.45;
    color: var(--ink-soft);
  }
  .contact-label {
    display: inline-block;
    width: 20px;
    color: var(--accent);
  }
  .address {
    position: absolute;
    left: 318px;
    top: 188px;
    font-size: 13px;
    line-height: 1.4;
    color: var(--ink-soft);
    font-style: normal;
  }

  /* Back */
  .back-brand {
    position: absolute;
    left: 0;
    right: 0;
    top: 92px;
    display: flex;
    align-items: center;
    justify-content: center;
    gap: 16px;
  }
  .back-brand .brand-dot { width: 44px; height: 44px; }
  .back-brand .brand-name { font-size: 50px; }
  .back-web {
    position: absolute;
    right: 40px;
    bottom: 38px;
    font-size: 16px;
    letter-spacing: 3.5px;
  }
  .back-web .web-accent { color: var(--accent); }
</style>
</head>
<body>
<main class="sheet">
  <section class="card card-front">
    <div class="brand">
      <span class="brand-dot"></span>
      <span class="brand-name">RB Tolvane</span>
    </div>
    <p class="tagline">trusted builds, planned right</p>
    <div class="person">
      <p class="person-name">Your Name</p>
      <p class="person-title">Title</p>
    </div>
    <p class="web">www.rb<span class="web-accent">tolvane</span>.com</p>
    <span class="divider"></span>
    <ul class="contact">
      <li><span class="contact-label">P:</span>123-456-7890</li>
      <li><span class="contact-label">C:</span>123-456-7890</li>
      <li><span class="contact-label">E:</span>info@rbtolvane.com</li>
    </ul>
    <address class="address">Door No. Street Name<br>City Name, State, Zip Code</address>
  </section>

  <section class="card card-back">
    <div class="back-brand">
      <span class="brand-dot"></span>
      <span class="brand-name">RB Tolvane</span>
    </div>
    <p class="back-web">www.rb<span class="web-accent">tolvane</span>.com</p>
  </section>
</main>
</body>
</html>
```